2015 Conference Header

I would like a header designed for our conference next year. It will be used on all of our event promotional material. The information and images that can be used are in the drop box file. I have also included examples of what we have used in the past.

https://www.filecrate.net/sh/7k2m4qwe9zt1pl/BXtRf834pLmnWqYz2cVbH9sDo?dl=0

Industry/Entity Type

Event

Requirements
Must have
• To give you all a little more idea on our branding colours and designs our business website is www.curvellaforms.com

```html
<!DOCTYPE html>
<html lang="en">
<head>
<meta charset="utf-8">
<title>Curvella 2015 Conference Header</title>
<link rel="stylesheet" href="https://fonts.googleapis.com/css2?family=Mulish:wght@400;700&display=swap">
<style>
  :root {
    --page-bg: #e9ecef;
    --panel-light: #f4f4f4;
    --panel-shade: #d9d9d9;
    --brand-orange: #d9832b;
    --brand-dark: #3a2a1c;
    --text-dark: #333333;
    --photo-green: #6f8f4e;
    --photo-sky: #c9d6c4;
  }
  * { margin: 0; padding: 0; box-sizing: border-box; }
  html, body {
    width: 1200px;
    height: 900px;
    overflow: hidden;
    background: var(--page-bg);
  }
  .conference-header {
    position: absolute;
    left: 40px;
    top: 203px;
    width: 1120px;
    height: 494px;
    border-radius: 24px;
    overflow: hidden;
    box-shadow: 0 6px 22px rgba(0,0,0,0.18);
    background: var(--panel-light);
  }
  .header-art {
    position: absolute;
    inset: 0;
    width: 100%;
    height: 100%;
  }
  .event-details {
    position: absolute;
    left: 680px;
    top: 0;
    width: 420px;
    height: 100%;
    text-align: center;
    font-family: "Mulish", sans-serif;
    color: var(--text-dark);
  }
  .event-name {
    position: absolute;
    top: 110px;
    width: 100%;
    font-size: 44px;
    font-weight: 700;
    letter-spacing: 2px;
    line-height: 1.2;
    color: var(--brand-orange);
  }
  .event-year {
    position: absolute;
    top: 170px;
    width: 100%;
    font-size: 40px;
    line-height: 1.2;
  }
  .event-place {
    position: absolute;
    top: 262px;
    width: 100%;
    font-size: 32px;
    line-height: 1.2;
  }
  .event-dates {
    position: absolute;
    top: 308px;
    width: 100%;
    font-size: 32px;
    line-height: 1.2;
  }
  .details-rule {
    position: absolute;
    top: 396px;
    left: 30px;
    width: 360px;
    height: 3px;
    background: var(--brand-orange);
  }
  .event-url {
    position: absolute;
    top: 410px;
    width: 100%;
    font-size: 20px;
    line-height: 1.2;
    letter-spacing: 0.5px;
  }
</style>
</head>
<body>
  <section class="conference-header">
    <svg class="header-art" viewBox="0 0 1120 494" preserveAspectRatio="none">
      <defs>
        <linearGradient id="photoTone" x1="0" y1="0" x2="0" y2="1">
          <stop offset="0" stop-color="var(--photo-sky)"/>
          <stop offset="0.35" stop-color="var(--photo-green)"/>
          <stop offset="1" stop-color="#4f6b3a"/>
        </linearGradient>
        <linearGradient id="panelTone" x1="0" y1="0" x2="1" y2="0">
          <stop offset="0" stop-color="var(--panel-shade)"/>
          <stop offset="0.25" stop-color="var(--panel-light)"/>
          <stop offset="1" stop-color="var(--panel-light)"/>
        </linearGradient>
      </defs>
      <rect class="event-photo" role="img" aria-label="Photo of conference guests strolling through a vineyard with glasses of wine" x="0" y="0" width="700" height="494" fill="url(#photoTone)"/>
      <path class="divider-dark" d="M600,0 C585,110 650,170 612,232 C590,300 612,420 590,494 L700,494 L700,0 Z" fill="var(--brand-dark)"/>
      <path class="divider-orange" d="M628,0 C612,110 676,170 638,232 C616,300 638,420 616,494 L720,494 L720,0 Z" fill="var(--brand-orange)"/>
      <path class="details-panel" d="M650,0 C634,110 698,170 660,232 C638,300 660,420 638,494 L1120,494 L1120,0 Z" fill="url(#panelTone)"/>
    </svg>
    <div class="event-details">
      <h1 class="event-name">CURVELLA</h1>
      <p class="event-year">2015</p>
      <p class="event-place">Adelaide, Australia</p>
      <p class="event-dates">21 - 23 June</p>
      <div class="details-rule"></div>
      <p class="event-url">www.curvellaconference.com.au</p>
    </div>
  </section>
</body>
</html>
```